Dultavo.com webside

I want to build a Dultavo.com retail website use on Shopify, reselling three main categories: Office Supplies, Packing Supplies, and Home Consumables. I also wish the webpage has the same functions as the Zelvik home page. The page is split into three different parts with the top being a sliding screen showcasing promotion products, below it being the three categories, and finally, a moving screen showing company missions.
Target Market(s)
U.S online
Industry/Entity Type
Office Supplies, packing Supplies and Home Consumables
Coding
Coded - Design and coding required
Number of Pages Required
5+ page
Look and feel

```html
<!DOCTYPE html>
<html lang="en">
<head>
<meta charset="utf-8">
<title>Dultavo — Office, Packing &amp; Home Supplies</title>
<link href="https://fonts.googleapis.com/css2?family=Montserrat:wght@300;400;500;600;700;800&display=swap" rel="stylesheet">
<style>
:root{
  --green:#0f6b4e;
  --ink:#1c1c1c;
  --muted:#5a5a5a;
  --line:#d9dedc;
  --footer:#f6f8f7;
  --white:#ffffff;
}
*{box-sizing:border-box;margin:0;padding:0}
html,body{width:1200px;height:3760px;overflow:hidden;background:var(--white)}
body{font-family:'Montserrat',sans-serif;color:var(--ink);position:relative}
.abs{position:absolute}

/* header */
.site-header{left:0;top:0;width:1200px;height:118px}
.logo{left:80px;top:52px;font-weight:800;font-size:26px;letter-spacing:3px;color:var(--ink)}
.main-nav{left:226px;top:58px;display:flex;gap:26px;font-size:13px;color:var(--ink)}
.main-nav span::after{content:" ▾";font-size:10px}
.header-icons{right:82px;top:54px;display:flex;gap:18px}

/* hero */
.hero{left:0;top:118px;width:1200px;height:580px;background:radial-gradient(ellipse at center,#f4f2ee 0%,#e9e6e0 55%,#cfccc6 100%)}
.hero-content{left:0;top:178px;width:1200px;text-align:center}
.hero-title{font-weight:300;font-size:68px;color:#222}
.hero-title b{font-weight:800;color:var(--green)}
.hero-sub{margin-top:18px;font-weight:600;font-size:17px;color:#222}
.btn-shop{display:inline-block;margin-top:34px;border:2px solid var(--green);padding:8px 16px;font-size:17px;color:var(--green);background:rgba(255,255,255,.4)}

/* promo */
.section-title{font-weight:700;font-size:30px;color:var(--green)}
.promo-title{left:112px;top:768px}
.product{width:226px}
.product .ph{width:226px;height:250px}
.product .name{margin-top:12px;font-size:13px;color:var(--ink)}
.product .price{margin-top:4px;font-size:15px;color:var(--ink)}

/* categories */
.cat-img{}
.cat-label{font-size:17px;color:var(--green);display:flex;align-items:center;gap:12px}
.view-more{font-size:11px;color:var(--ink)}

/* about */
.about-col{width:420px;text-align:center}
.about-col h2{font-weight:700;font-size:30px;color:var(--green)}
.about-col p{margin-top:28px;font-size:16px;line-height:30px;color:var(--green)}

/* video */
.video{left:112px;top:2660px;width:976px;height:556px;background:linear-gradient(135deg,#f2a37d 0%,#e9835e 40%,#d8b58c 75%,#f0c9a8 100%)}
.play{left:500px;top:2848px}

/* footer */
.site-footer{left:0;top:3272px;width:1200px;height:488px;background:var(--footer);border-top:2px solid #cfe0d9}
.f-col h3{font-weight:700;font-size:15px;color:var(--ink)}
.f-col ul{list-style:none;margin-top:26px}
.f-col li{font-size:13px;line-height:30px;color:var(--green)}
.f-col p{margin-top:26px;font-size:13px;line-height:26px;color:var(--green);width:260px}
.subscribe-label{left:180px;top:3512px;font-size:13px;color:var(--muted)}
.email-box{left:180px;top:3552px;width:362px;height:50px;border:1px solid #9aa5a0;background:var(--white);font-size:13px;color:#888;padding:16px 18px}
.email-box .arrow{position:absolute;right:16px;top:14px}
.socials{left:856px;top:3572px;display:flex;gap:14px;font-size:11px;font-weight:600;color:var(--green)}
.payments{left:180px;top:3680px;display:flex;gap:12px}
.pay{width:38px;height:24px;border:1px solid #c9cfcc;border-radius:3px;background:var(--white);font-size:8px;font-weight:600;color:var(--ink);display:flex;align-items:center;justify-content:center}
.copyright{left:180px;top:3730px;font-size:12px;color:var(--green)}
.currency{left:1136px;top:3732px;font-size:10px;color:var(--muted)}
</style>
</head>
<body>

<header class="site-header abs">
  <div class="logo abs">DULTAVO</div>
  <nav class="main-nav abs"><span>Office Supplies</span><span>Packing Supplies</span><span>Home Consumables</span></nav>
  <div class="header-icons abs">
    <svg width="18" height="18" viewBox="0 0 18 18" fill="none" stroke="#222" stroke-width="1.6"><circle cx="7.5" cy="7.5" r="5.5"/><path d="M12 12l5 5"/></svg>
    <svg width="18" height="18" viewBox="0 0 18 18" fill="none" stroke="#222" stroke-width="1.6"><circle cx="9" cy="6" r="4"/><path d="M2 17c1-4 4-6 7-6s6 2 7 6"/></svg>
    <svg width="18" height="18" viewBox="0 0 18 18" fill="none" stroke="#222" stroke-width="1.6"><path d="M2 5h14l-1.5 11h-11z"/><path d="M6 5a3 3 0 016 0"/></svg>
  </div>
</header>

<section class="hero abs" role="img" aria-label="Desk flat lay with notebooks, magnifier, pens and glue on a light surface"></section>
<div class="hero-content abs">
  <h1 class="hero-title">Welcome to <b>DULTAVO</b></h1>
  <p class="hero-sub">We are Suppliers of Office Supplies, Packing Supplies and Home Consumables</p>
  <span class="btn-shop">Shop Now</span>
</div>

<h2 class="section-title promo-title abs">Promotional Products</h2>

<div class="product abs" style="left:112px;top:832px"><div class="ph" role="img" aria-label="Office files in green folders" style="background:linear-gradient(135deg,#cfe3a8,#7fb34a 60%,#e8e8e0)"></div><p class="name">Office Files</p><p class="price">$10</p></div>
<div class="product abs" style="left:364px;top:832px"><div class="ph" role="img" aria-label="Colourful office pens" style="background:linear-gradient(135deg,#e84a6a,#f0b62a 35%,#3a8fd8 70%,#8a4ad0)"></div><p class="name">Office Pens</p><p class="price">$10</p></div>
<div class="product abs" style="left:612px;top:832px"><div class="ph" role="img" aria-label="Rolls of soft tissues" style="background:linear-gradient(135deg,#f4f4f4,#dcdcdc 60%,#c4c4c4)"></div><p class="name">Soft Tissues</p><p class="price">$10</p></div>
<div class="product abs" style="left:864px;top:832px"><div class="ph" role="img" aria-label="Rows of AA batteries" style="background:linear-gradient(135deg,#c8c2b4,#8c8474 55%,#d8d2c4)"></div><p class="name">AA Batteries</p><p class="price">$10</p></div>

<div class="product abs" style="left:112px;top:1188px"><div class="ph" role="img" aria-label="Desk document holder" style="background:linear-gradient(135deg,#e4f2f4,#9ccdd4 55%,#f2f2ee)"></div><p class="name">Hover Board</p><p class="price">$16</p></div>
<div class="product abs" style="left:364px;top:1188px"><div class="ph" role="img" aria-label="Stapler on a desk" style="background:linear-gradient(135deg,#6a5a4e,#b04a3a 50%,#3a3a44)"></div><p class="name">Stapler</p><p class="price">$19</p></div>
<div class="product abs" style="left:612px;top:1188px"><div class="ph" role="img" aria-label="Color pencils in a clear cup" style="background:linear-gradient(135deg,#f6f6f6,#e8c25a 40%,#d85a4a 65%,#5a8ad0)"></div><p class="name">Color Pencils</p><p class="price">$10</p></div>
<div class="product abs" style="left:864px;top:1188px"><div class="ph" role="img" aria-label="Stack of A4 paper sheets" style="background:linear-gradient(135deg,#fafafa,#e2e2e2 60%,#cacaca)"></div><p class="name">A4 Sheets</p><p class="price">$27</p></div>

<div class="cat-img abs" role="img" aria-label="Office supplies: pencils in a cup, books and stationery on a desk" style="left:112px;top:1624px;width:570px;height:618px;background:linear-gradient(135deg,#6a4a34,#c88a4a 35%,#e0b25a 55%,#3a4a6a 80%,#8a6a54)"></div>
<div class="cat-img abs" role="img" aria-label="Packing supplies: stretch wrap and boxes" style="left:700px;top:1624px;width:388px;height:282px;background:linear-gradient(135deg,#e8e6e2,#c4c0b8 55%,#9a8c78)"></div>
<div class="cat-img abs" role="img" aria-label="Home consumables: cleaning products on a table" style="left:700px;top:1996px;width:388px;height:246px;background:linear-gradient(135deg,#f0ede8,#d8d2c8 50%,#4ab0d0 75%,#e8e4de)"></div>

<div class="cat-label abs" style="left:700px;top:1926px">Packing Supplies <svg width="26" height="12" viewBox="0 0 26 12" fill="none" stroke="#222" stroke-width="1.6"><path d="M0 6h24M19 1l5 5-5 5"/></svg></div>
<div class="view-more abs" style="left:700px;top:1952px">View More</div>
<div class="cat-label abs" style="left:112px;top:2266px">Office Supplies <svg width="26" height="12" viewBox="0 0 26 12" fill="none" stroke="#222" stroke-width="1.6"><path d="M0 6h24M19 1l5 5-5 5"/></svg></div>
<div class="cat-label abs" style="left:700px;top:2266px">Home Consumables <svg width="26" height="12" viewBox="0 0 26 12" fill="none" stroke="#222" stroke-width="1.6"><path d="M0 6h24M19 1l5 5-5 5"/></svg></div>

<div class="about-col abs" style="left:130px;top:2380px">
  <h2>DULTAVO</h2>
  <p>Lorem Ipsum is simply dummy text of the printing and typesetting industry. Lorem Ipsum has been the industry's standard dummy text ever since the 1500s.</p>
</div>
<div class="about-col abs" style="left:630px;top:2380px">
  <h2>OUR MISSION</h2>
  <p>It is a long established fact that a reader will be distracted by the readable content of a page when looking at its layout. The point of using Lorem Ipsum is that it has a more-or-less</p>
</div>

<div class="video abs" role="img" aria-label="Video still: stationery tray with pencils, paper clips and pins"></div>
<svg class="play abs" width="200" height="180" viewBox="0 0 200 180"><circle cx="100" cy="90" r="48" fill="#ffffff"/><path d="M88 68v44l36-22z" fill="#e9835e"/></svg>

<footer class="site-footer abs"></footer>
<div class="f-col abs" style="left:180px;top:3338px"><h3>Quick Links</h3><ul><li>Office Supplies</li><li>Packing Supplies</li><li>Home Consumables</li></ul></div>
<div class="f-col abs" style="left:532px;top:3338px"><h3>Info</h3><ul><li>About</li><li>Contact Us</li><li>Shipping Policy</li><li>Blog</li></ul></div>
<div class="f-col abs" style="left:856px;top:3338px"><h3>DULTAVO</h3><p>Quality materials, good designs, craftsmanship and sustainability.</p></div>

<div class="subscribe-label abs">Subscribe to our emails</div>
<div class="email-box abs">Email<svg class="arrow" width="18" height="12" viewBox="0 0 18 12" fill="none" stroke="#222" stroke-width="1.5"><path d="M0 6h16M11 1l5 5-5 5"/></svg></div>

<div class="socials abs"><span>Chirpa</span><span>Folko</span><span>Snapla</span><span>Tiko</span><span>Vidra</span></div>

<div class="payments abs">
  <span class="pay">Velo</span><span class="pay">Merca</span><span class="pay">Orbix</span><span class="pay">Payvo</span><span class="pay">Quanta</span><span class="pay">Lumo</span>
</div>

<div class="copyright abs">Copyrights 2022@ Dultavo. All Rights Reserved</div>
<div class="currency abs">USD</div>

</body>
</html>
```